Business Card Design

WE are looking for a premium quality Business Cards for a Law Firm . Copies of our current business card is attached.

Contact Information for Business Card

xyz

```html
<!DOCTYPE html>
<html lang="en">
<head>
<meta charset="utf-8">
<title>Harcourt Legal – Business Cards</title>
<link href="https://fonts.googleapis.com/css2?family=Cinzel:wght@600&family=Arimo:wght@400;700&display=swap" rel="stylesheet">
<style>
  :root{
    --bg:#2b2b2b;
    --paper:#ffffff;
    --green:#063322;
    --gold:#b8965a;
    --ink:#1c1c1c;
    --text-light:#f2f2f2;
  }
  *{box-sizing:border-box;margin:0;padding:0}
  html,body{width:1200px;height:750px;overflow:hidden;background:var(--bg)}
  .canvas{position:relative;width:1200px;height:750px;font-family:"Arimo",Arial,sans-serif}
  .card{position:absolute;width:530px;height:303px;border-radius:18px;overflow:hidden}

  /* Front: offices */
  .card--offices{left:60px;top:110px;background:var(--paper);color:var(--ink)}
  .offices{position:absolute;left:40px;top:30px;font-size:12px;line-height:1.25}
  .office{margin-bottom:12px}
  .office:last-child{margin-bottom:0}
  .office__city{font-weight:700;font-size:13px}
  .office__phone b{font-weight:700}
  .brand{position:absolute;right:40px;top:86px;width:220px;display:flex;flex-direction:column;align-items:center;gap:14px}
  .brand__dot{width:60px;height:60px;border:3px solid var(--gold);border-radius:50%}
  .brand__name{font-family:"Arimo",Arial,sans-serif;font-weight:700;font-size:28px;color:var(--green);line-height:1;white-space:nowrap}

  /* Back: person */
  .card--person{left:610px;top:340px;background:var(--green);color:var(--text-light)}
  .seal{position:absolute;right:34px;top:26px;width:88px;height:88px;border-radius:50%;border:4px solid var(--gold)}
  .divider{position:absolute;left:30px;right:30px;top:176px;height:1px;background:var(--gold)}
  .person{position:absolute;left:30px;top:112px}
  .person__name{font-family:"Cinzel",serif;font-weight:600;font-size:22px;color:var(--gold);letter-spacing:.5px}
  .person__role{font-size:12.5px;line-height:1.3;margin-top:2px}
  .address{position:absolute;right:30px;top:120px;text-align:right;font-size:12.5px;line-height:1.35}
  .contacts{position:absolute;left:30px;top:192px;list-style:none;font-size:13px;line-height:1.55}
  .contacts li{display:flex;align-items:center;gap:10px}
  .contacts svg{width:12px;height:12px;fill:var(--gold);flex:none}
</style>
</head>
<body>
<main class="canvas">

  <section class="card card--offices">
    <div class="offices">
      <div class="office">
        <div class="office__city">Melbourne</div>
        <div>Level 12, 48 Ardent Street</div>
        <div>Melbourne, VIC 3000</div>
        <div class="office__phone"><b>Phone :</b> +61 03 5550 1200</div>
      </div>
      <div class="office">
        <div class="office__city">Sydney</div>
        <div>Level 9, Meridian House</div>
        <div>22 Harbour Lane</div>
        <div>Parramatta, NSW 2150</div>
        <div class="office__phone"><b>Phone :</b> +61 02 5550 1300</div>
      </div>
      <div class="office">
        <div class="office__city">Perth</div>
        <div>Level 6, Kestrel Tower</div>
        <div>75 Riverside Terrace</div>
        <div>Perth, WA 6000</div>
        <div class="office__phone"><b>Phone :</b> +61 08 5550 1400</div>
      </div>
    </div>
    <div class="brand">
      <div class="brand__dot"></div>
      <div class="brand__name">Harcourt Legal</div>
    </div>
  </section>

  <section class="card card--person">
    <div class="seal"></div>
    <div class="person">
      <div class="person__name">DANIEL MERCER</div>
      <div class="person__role">Director &amp; Principal Solicitor<br>MBA, Juris Doctor</div>
    </div>
    <div class="address">Level 3, Harcourt House<br>210 Lindell Terrace<br>Spring Hill, QLD 4000</div>
    <div class="divider"></div>
    <ul class="contacts">
      <li><svg viewBox="0 0 24 24"><path d="M6.6 10.8a15.2 15.2 0 0 0 6.6 6.6l2.2-2.2c.3-.3.7-.4 1-.2 1.1.4 2.3.6 3.6.6.6 0 1 .4 1 1V20c0 .6-.4 1-1 1A17 17 0 0 1 3 4c0-.6.4-1 1-1h3.5c.6 0 1 .4 1 1 0 1.3.2 2.5.6 3.6.1.3 0 .7-.2 1z"/></svg>+61 7 5550 1500</li>
      <li><svg viewBox="0 0 24 24"><path d="M7 1h10a2 2 0 0 1 2 2v18a2 2 0 0 1-2 2H7a2 2 0 0 1-2-2V3a2 2 0 0 1 2-2zm0 3v14h10V4zm5 15.5a1 1 0 1 0 0 2 1 1 0 0 0 0-2z"/></svg>+61 0400 555 018</li>
      <li><svg viewBox="0 0 24 24"><path d="M2 5h20v14H2zm2 2v.5l8 5 8-5V7l-8 5z"/></svg>daniel@harcourtlegal.com.au</li>
      <li><svg viewBox="0 0 24 24"><path d="M12 2a10 10 0 1 0 0 20 10 10 0 0 0 0-20zm0 2c1 1.3 1.8 3.1 2.1 5H9.9c.3-1.9 1.1-3.7 2.1-5zM4.3 13a8 8 0 0 1 0-2h3.6a16 16 0 0 0 0 2zm5.6 0a14 14 0 0 1 0-2h4.2a14 14 0 0 1 0 2zm6.2 0a16 16 0 0 0 0-2h3.6a8 8 0 0 1 0 2zM12 20c-1-1.3-1.8-3.1-2.1-5h4.2c-.3 1.9-1.1 3.7-2.1 5z"/></svg>www.harcourtlegal.com.au</li>
    </ul>
  </section>

</main>
</body>
</html>
```